Custom Wordpress Theme - Original and Professional

We are a boutique Harbourline IT that provide small and medium business in Australia three different levels of IT service.
We are looking for a developer who will create a customised, original and professional wordpress theme. We are looking for the developer to create a professional, clean, clear and simple theme with a stylish layout, images and icons.
Our three services are: IT support | IT Services | IT Solutions and we would like to clearly differentiate the difference in each level of service in as few words as possible.
IT Support is the ad hock “call us, when you need us” service, that smaller business or those with minimal issues use.
IT service is the unlimited service, that business with existing (and well maintained) IT systems choose and is both flexible and scalable including no contracts or paperwork required.
IT solutions are the unlimited service that businesses that need new or updated infrastructure choose and it includes all the hardware, software and services with no contracts or any ongoing commitment.
The main page on the web site will attract the visitor to choose the right “service level” for their business and then we will have a dedicated page for each service and another page for a comparison (table) to compare all three services.
Lastly we will need a contact us page that has both office locations (Sydney and Melbourne), contact phone numbers and an email form.
Items we are focused on for this project are: 1. Images, 2.Icons 3. Layout.
In summary we are looking for a custom WordPress theme into a 6 page (Home, IT Support, IT Services, IT Solutions, Compare Service levels and Contact us) website. The design must include relevant images and icons and be clear, simple, professional and sleek.

Thank you for your time and creativity and I look forward to working with you!

Target Market(s)

Small and Medium businesses in Australia

Industry/Entity Type

Boutique

Requirements
Must have
• - 6 Pages layout: Home, IT support, IT services, IT Solutions, Compare service levels and Contact us
- Images, Layout and Icons.
- Clean, Clear, Simple, Elegant, Stylish.
Nice to have
• - Some text (if possible but not required).
Should not have
• - Complexity.
- Confusing layout.
- Generic non matching images and icons.

```html
<!DOCTYPE html>
<html lang="en">
<head>
<meta charset="utf-8">
<title>Harbourline IT — Home</title>
<link href="https://fonts.googleapis.com/css2?family=Source+Sans+3:wght@400;600;700&family=PT+Sans+Narrow&family=Arimo:wght@400&display=swap" rel="stylesheet">
<style>
  :root {
    --brand-blue: #17517a;
    --brand-blue-deep: #124466;
    --ink: #222;
    --body-text: #444;
    --band-top: #d6d6d6;
    --band-bottom: #ececec;
    --nav-top: #6a6a6c;
    --nav-bottom: #3f3f41;
    --footer: #4d4d4f;
    --footer-bottom: #2b2b2b;
    --footer-text: #f0f0f0;
    --muted-logo: #a8a8a8;
  }
  * { margin: 0; padding: 0; box-sizing: border-box; }
  html, body { width: 1200px; height: 1114px; overflow: hidden; background: #fff; }
  body { font-family: "Source Sans 3", sans-serif; color: var(--ink); }
  .page { position: relative; width: 1200px; height: 1114px; overflow: hidden; background: #fff; }

  .brand { position: absolute; display: flex; align-items: center; gap: 12px; }
  .brand-mark { width: 14px; height: 14px; border-radius: 50%; background: var(--brand-blue); }
  .brand-name { font-family: "Source Sans 3", sans-serif; font-weight: 400; font-size: 40px; color: var(--brand-blue); letter-spacing: 0.5px; }
  .header-brand { left: 203px; top: 66px; }

  .language { position: absolute; left: 731px; top: 87px; display: flex; align-items: center; gap: 8px; font-family: "Arimo", sans-serif; font-size: 11.5px; color: #222; }
  .language-select { position: relative; width: 135px; height: 21px; border: 1px solid #d4d4d4; background: linear-gradient(#fff, #f1f1f1); padding: 3px 6px; font-size: 11.5px; }
  .language-select .arrow { position: absolute; right: 0; top: 0; width: 22px; height: 19px; background: var(--brand-blue); }
  .language-select svg { position: absolute; left: 6px; top: 6px; }

  .hero-band { position: absolute; left: 0; top: 191px; width: 1200px; height: 346px; background: linear-gradient(var(--band-top), var(--band-bottom)); }

  .main-nav { position: absolute; left: 203px; top: 159px; width: 793px; height: 62px; border-radius: 8px; background: linear-gradient(var(--nav-top), var(--nav-bottom)); box-shadow: 0 2px 4px rgba(0,0,0,0.25); }
  .main-nav a { position: absolute; top: 20px; font-family: "PT Sans Narrow", sans-serif; font-size: 17px; color: #fff; text-decoration: none; text-shadow: 0 1px 1px rgba(0,0,0,0.5); }
  .nav-dot { position: absolute; top: 24px; width: 13px; height: 13px; border-radius: 50%; border: 3px solid #fff; background: #4a4a4c; }

  .hero-title { position: absolute; left: 203px; top: 306px; font-size: 47px; font-weight: 700; color: var(--brand-blue); letter-spacing: -0.3px; }
  .hero-tagline { position: absolute; left: 202px; top: 363px; font-size: 17px; font-weight: 600; color: #222; letter-spacing: 1.6px; }
  .hero-visual { position: absolute; left: 624px; top: 276px; width: 576px; height: 171px; background: linear-gradient(90deg, rgba(215,215,215,0) 0%, #bfc4c8 30%, #9aa3aa 55%, #cfd1d3 80%, rgba(230,230,230,0) 100%); border-radius: 4px; }

  .service { position: absolute; top: 474px; width: 241px; }
  .service-image { width: 241px; height: 122px; border: 2px solid var(--brand-blue); }
  .service-title { margin-top: 10px; height: 32px; background: var(--brand-blue); color: #fff; font-size: 16.5px; padding: 5px 7px; }
  .service-text { margin-top: 7px; font-family: "Arimo", sans-serif; font-size: 11.3px; line-height: 13.8px; color: var(--body-text); text-align: justify; }

  .footer { position: absolute; left: 0; top: 759px; width: 1200px; height: 242px; background: linear-gradient(#464648, var(--footer) 40%, #575759); }
  .footer-heading { position: absolute; top: 16px; font-size: 23px; font-weight: 700; color: var(--footer-text); }
  .social { position: absolute; top: 86px; width: 46px; height: 46px; border-radius: 50%; border: 2px solid #ddd; }
  .blog-item { position: absolute; left: 457px; width: 235px; }
  .blog-item .bullet { position: absolute; left: 0; top: 2px; width: 10px; height: 10px; border-radius: 50%; border: 2.5px solid #fff; }
  .blog-item p { margin-left: 15px; font-size: 11px; line-height: 13.7px; color: #fff; text-align: justify; }
  .button { position: absolute; top: 197px; width: 84px; height: 23px; border-radius: 4px; background: linear-gradient(#fff, #cfcfcf); box-shadow: 0 2px 3px rgba(0,0,0,0.4); font-family: "PT Sans Narrow", sans-serif; font-size: 14px; color: #222; text-align: center; line-height: 23px; }
  .contact-box { position: absolute; left: 755px; top: 62px; width: 241px; height: 125px; background: #fff; border: 2px solid #ddd; box-shadow: inset 0 0 12px rgba(0,0,0,0.25); padding: 6px 9px; font-size: 11px; line-height: 13.7px; color: #222; text-align: justify; }

  .footer-bottom { position: absolute; left: 0; top: 1001px; width: 1200px; height: 113px; background: var(--footer-bottom); }
  .copyright { position: absolute; left: 203px; top: 37px; font-size: 12px; line-height: 21px; color: #fff; }
  .footer-brand { right: 205px; top: 38px; }
  .footer-brand .brand-name { color: var(--muted-logo); font-size: 34px; }
  .footer-brand .brand-mark { background: var(--muted-logo); }
</style>
</head>
<body>
<div class="page">

  <header>
    <div class="brand header-brand">
      <span class="brand-mark"></span>
      <span class="brand-name">Harbourline IT</span>
    </div>
    <div class="language">
      <span>Choose Your language:</span>
      <div class="language-select">English
        <span class="arrow"><svg width="10" height="8" viewBox="0 0 10 8"><path d="M0 0 H10 L5 8 Z" fill="#fff"/></svg></span>
      </div>
    </div>
  </header>

  <div class="hero-band"></div>

  <nav class="main-nav">
    <a style="left:63px">HOME</a>
    <span class="nav-dot" style="left:145px"></span>
    <a style="left:200px">OFFER</a>
    <span class="nav-dot" style="left:283px"></span>
    <a style="left:335px">ABOUT US</a>
    <span class="nav-dot" style="left:444px"></span>
    <a style="left:495px">EXPERIENCE</a>
    <span class="nav-dot" style="left:616px"></span>
    <a style="left:667px">CONTACT</a>
  </nav>

  <section class="hero">
    <h1 class="hero-title">Harbourline IT</h1>
    <p class="hero-tagline">Your Hardware, Software Solution provider</p>
    <div class="hero-visual" role="img" aria-label="Laptop, desktop tower and monitor product shot"></div>
  </section>

  <section class="services">
    <article class="service" style="left:203px">
      <div class="service-image" role="img" aria-label="Support agent with headset at a workstation" style="background:linear-gradient(120deg,#cfd6dc,#8e9aa4 55%,#e6e6e6)"></div>
      <h2 class="service-title">IT Support</h2>
      <p class="service-text">IT Support is the ad hock “call us, when you need us” service, that smaller business or those with minimal issues use.</p>
    </article>
    <article class="service" style="left:480px">
      <div class="service-image" role="img" aria-label="Hand touching a cloud network interface" style="background:linear-gradient(120deg,#0e3a5c,#1b6fa0 50%,#0b2d48)"></div>
      <h2 class="service-title">IT Services</h2>
      <p class="service-text">IT service is the unlimited service, that business with existing (and well maintained) IT systems choose and is both flexible and scalable including no contracts or paperwork required.</p>
    </article>
    <article class="service" style="left:755px">
      <div class="service-image" role="img" aria-label="Blue keyboard with a solutions key" style="background:linear-gradient(120deg,#0a4c74,#1e9bd0 55%,#0b5a86)"></div>
      <h2 class="service-title">IT Solutions</h2>
      <p class="service-text">IT solutions are the unlimited service that businesses that need new or updated infrastructure choose and it includes all the hardware, software and services with no contracts or any ongoing commitment.</p>
    </article>
  </section>

  <footer class="footer">
    <h3 class="footer-heading" style="left:203px">Follow us</h3>
    <span class="social" style="left:206px;background:linear-gradient(#6a86c4,#3b5591)" aria-label="Social profile one"></span>
    <span class="social" style="left:266px;background:linear-gradient(#6fd0f2,#1f8fc4)" aria-label="Social profile two"></span>
    <span class="social" style="left:326px;background:linear-gradient(#e8776a,#b8342a)" aria-label="Social profile three"></span>

    <h3 class="footer-heading" style="left:452px">Blogs</h3>
    <div class="blog-item" style="top:62px"><span class="bullet"></span><p>Lorem Ipsum has been the industry's standard dummy text ever since the 1500s, when an unknown printer took a galley of type and scrambled it to make a type specimen book.</p></div>
    <div class="blog-item" style="top:130px"><span class="bullet"></span><p>Lorem Ipsum has been the industry's standard dummy text ever since the 1500s, when an unknown printer took a galley of type and scrambled it to make a type specimen book.</p></div>
    <span class="button" style="left:471px">SEE MORE</span>

    <h3 class="footer-heading" style="left:755px">Contact us</h3>
    <div class="contact-box">Lorem Ipsum has been the industry's standard dummy text ever since the 1500s, when an unknown printer took a galley of type and scrambled it to make a type specimen book.</div>
    <span class="button" style="left:912px">SEND</span>
  </footer>

  <div class="footer-bottom">
    <p class="copyright">Harbourline IT © 2013 All Right Reserved.<br>Created By : Harbourline IT</p>
    <div class="brand footer-brand">
      <span class="brand-mark"></span>
      <span class="brand-name">Harbourline IT</span>
    </div>
  </div>

</div>
</body>
</html>
```